Request for Business Card Design

Hi. My name is Marlene, I am looking for a new business card design for my company, Quarrow Signal Instruments, LLC. I really like the design you did for Tarsel Venture and was hoping you could do something similar using our full logo and our mark. I am also open to any raised texture design using our mark. I have attached our full logo, which would need to be somewhere on the card, as well as the mark in both outline and full form, as well as our brand colors / guide. The card does not have to be white, as long as our logo and mark appear. I actually like darker colored business cards more, but am open to all options. If you are interested in working with me, please let me know. We would also take the business card design into letterhead design if you can do that.

```html
<!DOCTYPE html>
<html lang="en">
<head>
<meta charset="utf-8">
<title>Quarrow Signal Instruments — Business Card</title>
<link href="https://fonts.googleapis.com/css2?family=Open+Sans:wght@400;600;700;800&display=swap" rel="stylesheet">
<style>
  :root{
    --stage:#1d1e21;
    --card-front:#3a3a3d;
    --card-back:#2c2c2f;
    --brand-blue:#1592bd;
    --white:#ffffff;
    --soft-white:#e9e9ea;
    --pattern-light:#4a4a4e;
    --pattern-dark:#242427;
  }
  *{margin:0;padding:0;box-sizing:border-box}
  html,body{width:1200px;height:780px;overflow:hidden}
  body{background:var(--stage);font-family:"Open Sans",Arial,sans-serif;position:relative}

  .card{position:absolute;top:235px;width:540px;height:309px;border-radius:4px;overflow:hidden;box-shadow:0 14px 30px rgba(0,0,0,.45)}
  .card--front{left:40px;background:var(--card-front)}
  .card--back{left:620px;background:var(--card-back)}

  .front-swoosh{position:absolute;inset:0;width:540px;height:309px}

  .brand{position:absolute;display:flex;align-items:center;gap:12px;color:var(--white)}
  .brand__dot{border-radius:50%;background:var(--brand-blue);flex:none}
  .brand__name{font-weight:700;line-height:1;letter-spacing:.08em}
  .brand__name small{display:block;font-size:.3em;letter-spacing:.12em;margin-top:5px}

  .card--front .brand{left:250px;top:44px}
  .card--front .brand__dot{width:44px;height:44px}
  .card--front .brand__name{font-size:32px}

  .person{position:absolute;left:118px;top:132px;text-align:right;width:140px}
  .person__name{font-size:34px;font-weight:700;color:var(--brand-blue);line-height:1}
  .person__role{font-size:14px;color:var(--soft-white);margin-top:4px}

  .divider{position:absolute;left:272px;top:132px;width:2px;height:86px;background:var(--soft-white)}

  .contacts{position:absolute;left:290px;top:140px;list-style:none}
  .contacts li{display:flex;align-items:center;gap:8px;font-size:13px;color:var(--white);line-height:18px}
  .contacts svg{width:12px;height:12px;flex:none;fill:var(--brand-blue)}

  .address{position:absolute;left:22px;top:256px;font-size:12px;color:var(--white);transform:rotate(9deg);transform-origin:left center;white-space:nowrap}

  .back-texture{position:absolute;inset:0;background:linear-gradient(120deg,var(--pattern-dark) 0%,var(--card-back) 45%,var(--pattern-light) 100%)}
  .card--back .brand{right:30px;bottom:28px;gap:8px}
  .card--back .brand__dot{width:20px;height:20px}
  .card--back .brand__name{font-size:15px}
</style>
</head>
<body>

<section class="card card--front" aria-label="Business card front">
  <svg class="front-swoosh" viewBox="0 0 540 309" aria-hidden="true">
    <path d="M0,185 C160,275 340,293 500,309 L0,309 Z" fill="var(--brand-blue)"/>
    <path d="M0,185 C160,275 340,293 500,309 L540,309 L540,304 C360,288 170,268 0,185 Z" fill="var(--brand-blue)" opacity="0"/>
    <path d="M22,170 C170,262 340,282 490,298" fill="none" stroke="var(--white)" stroke-width="3" stroke-linecap="round"/>
  </svg>

  <div class="brand">
    <span class="brand__dot"></span>
    <span class="brand__name">QUARROW<small>SIGNAL INSTRUMENTS</small></span>
  </div>

  <div class="person">
    <p class="person__name">Marlene</p>
    <p class="person__role">Director</p>
  </div>

  <span class="divider"></span>

  <ul class="contacts">
    <li><svg viewBox="0 0 24 24"><path d="M6.6 10.8a15 15 0 0 0 6.6 6.6l2.2-2.2c.3-.3.7-.4 1-.2 1.1.4 2.3.6 3.6.6.6 0 1 .4 1 1V20c0 .6-.4 1-1 1A17 17 0 0 1 3 4c0-.6.4-1 1-1h3.5c.6 0 1 .4 1 1 0 1.3.2 2.5.6 3.6.1.3 0 .7-.2 1z"/></svg>+001 555 214 7730</li>
    <li><svg viewBox="0 0 24 24"><path d="M6 3h9v5H6zM4 9h16v9h-3v3H7v-3H4zm5 7v3h6v-3z"/></svg>+001 555 214 7731</li>
    <li><svg viewBox="0 0 24 24"><path d="M12 2a10 10 0 1 0 0 20 10 10 0 0 0 0-20zm6.9 9h-3a15 15 0 0 0-1.3-5.6A8 8 0 0 1 18.9 11zM12 4c.9 1.2 1.8 3.6 1.9 7h-3.8c.1-3.4 1-5.8 1.9-7zM9.4 5.4A15 15 0 0 0 8.1 11h-3a8 8 0 0 1 4.3-5.6zM5.1 13h3a15 15 0 0 0 1.3 5.6A8 8 0 0 1 5.1 13zm6.9 7c-.9-1.2-1.8-3.6-1.9-7h3.8c-.1 3.4-1 5.8-1.9 7zm2.6-1.4a15 15 0 0 0 1.3-5.6h3a8 8 0 0 1-4.3 5.6z"/></svg>www.quarrowsignal.com</li>
    <li><svg viewBox="0 0 24 24"><path d="M3 5h18v14H3zm2 2v.5l7 4.5 7-4.5V7zm0 2.9V17h14V9.9l-7 4.5z"/></svg>info@quarrowsignal.com</li>
  </ul>

  <p class="address">1850 Fenwick Park Drive • Ashbury, CO 80611</p>
</section>

<section class="card card--back" aria-label="Business card back">
  <div class="back-texture" role="img" aria-label="Raised repeating brand-mark texture across the card"></div>
  <div class="brand">
    <span class="brand__dot"></span>
    <span class="brand__name">QUARROW<small>SIGNAL INSTRUMENTS</small></span>
  </div>
</section>

</body>
</html>
```